Association qui souhaite améliorer l'accès aux personnes en situation de handicap

Nous sommes une association qui a pour objectif d'améliorer l'accessibilité, augmenter l'offre des activités réalisables dans notre région touristique.
Nous souhaitons réaliser un site internet afin de pouvoir communiquer sur notre association. Nous avons déjà conçu notre flyer sur Plumotrix. Nous souhaiterions une base graphique se rapportant à celui-ci. C'est possible de tout retravailler mais nous souhaitons tout de même retrouver la charte graphique ou code couleur du flyer.
Il nous faudrait quelques pages:
- 1 page : Acceuil / Présentation (Home), Il y aurait le descriptif de l'association, avec ses objectifs à +/- moyen terme
- 1 page : Nos réalisations, celle-ci présenterait les éléments que nous avons réalisés avec des zones de textes et des images classées chronologiquement au fur et à mesure des nouveautés
- 1 page : Media, comme la précédente, mais ou on pourrait voir ou lire sur les divers médias qui parlent de nous
- 1 page : Evenements : c'est une page pour présenter divers activités que nous allons organiser
- 1 page : Contact qui indique comment nous contacter et avec la présentation des 5 ou 6 membres du comité
- 1 link donate : qui arrive sur un formulaire de donnée que l'on pourra faire évoluer sur un système de payement par la suite. Cette bannière doit se retrouver sur toutes les pages
Il est nécessaire que se design puisse être transféré sur une lecture sur téléphone mobile
Personnes en situation de handicap
Associatif

```html
<!DOCTYPE html>
<html lang="en">
<head>
<meta charset="utf-8">
<title>Contact Us – OpenPath Association</title>
<link rel="stylesheet" href="https://fonts.googleapis.com/css2?family=Raleway:wght@500;600;700;800&family=Mulish:wght@400;500;600&family=Oswald:wght@500&display=swap">
<style>
:root{
  --red:#c01a24;
  --ink:#1e1e1e;
  --text:#2b2b2b;
  --muted:#6b6b6b;
  --soft:#f4f5f9;
  --dark:#263034;
  --white:#ffffff;
}
*{box-sizing:border-box;margin:0;padding:0}
html,body{width:1200px;height:2259px;overflow:hidden}
body{position:relative;background:var(--white);font-family:"Mulish",sans-serif;color:var(--text)}
.abs{position:absolute}
.center{left:0;width:1200px;text-align:center}

.topbar{top:0;left:0;width:1200px;height:29px;background:var(--red);color:var(--white);font-size:11px}
.topbar .social-dot{position:absolute;left:130px;top:9px;width:10px;height:10px;border-radius:50%;background:var(--white)}
.topbar .mail{position:absolute;right:129px;top:7px;display:flex;align-items:center;gap:5px}

.header{top:29px;left:0;width:1200px;height:61px;background:var(--white);box-shadow:0 1px 3px rgba(0,0,0,.06)}
.brand{position:absolute;left:130px;top:20px;display:flex;align-items:center;gap:7px;font-family:"Raleway",sans-serif;font-weight:800;font-size:14px;line-height:1;color:var(--ink);text-transform:uppercase}
.brand .mark{width:22px;height:22px;background:var(--red)}
.nav{position:absolute;top:24px;font-size:11.5px;color:var(--ink);font-weight:500;white-space:nowrap}
.nav.active{color:var(--red)}
.nav.active svg{position:absolute;left:10px;top:15px}
.donate{position:absolute;left:977px;top:16px;width:93px;height:30px;border-radius:15px;background:var(--red);color:var(--white);font-weight:600;font-size:11px;display:flex;align-items:center;justify-content:center}

.hero{top:90px;left:0;width:1200px;height:272px;background:linear-gradient(135deg,#4b4f4b 0%,#5a5f58 40%,#4e524f 70%,#454945 100%)}
.hero-shade{position:absolute;inset:0;background:rgba(20,20,20,.35)}
.hero h1{position:absolute;top:104px;left:0;width:1200px;text-align:center;font-family:"Raleway",sans-serif;font-weight:800;font-size:35px;color:var(--white);letter-spacing:.5px}
.hero h1 span{color:var(--red)}
.crumb{position:absolute;top:151px;left:0;width:1200px;text-align:center;font-size:9.5px;color:#ddd}
.crumb b{font-weight:500;color:var(--white)}

.eyebrow{font-family:"Raleway",sans-serif;font-weight:500;font-size:16px;color:var(--ink)}
.title{font-family:"Raleway",sans-serif;font-weight:600;font-size:34px;color:var(--ink)}

.card{top:522px;width:300px;height:165px;border:1px solid #333;background:var(--white);text-align:center}
.card .icon{position:absolute;left:126px;top:33px;width:49px;height:49px;border-radius:50%;background:var(--red);display:flex;align-items:center;justify-content:center}
.card h3{position:absolute;top:96px;width:100%;font-family:"Raleway",sans-serif;font-weight:600;font-size:17px;color:var(--red)}
.card p{position:absolute;top:121px;width:100%;font-size:12px;color:var(--ink)}
.card.featured{background:var(--red);border-color:var(--red)}
.card.featured .icon{background:var(--white)}
.card.featured h3,.card.featured p{color:var(--white)}

.enquiry{top:766px;left:0;width:1200px;height:558px;background:var(--soft)}
.field{border:1px solid #333;font-size:12px;color:var(--text);padding:20px 0 0 19px}
.submit{left:404px;top:1211px;width:391px;height:57px;background:var(--red);color:var(--white);font-weight:600;font-size:12px;letter-spacing:.8px;display:flex;align-items:center;justify-content:center}

.member{top:1460px;width:220px}
.member .photo{height:234px}
.member h4{margin-top:13px;text-align:center;font-family:"Raleway",sans-serif;font-weight:500;font-size:17px;color:var(--ink)}
.member span{display:block;text-align:center;font-size:10.5px;color:var(--muted);margin-top:2px;letter-spacing:.3px}
.arrow{top:1559px;width:35px;height:35px;border-radius:50%;border:1px solid #333;display:flex;align-items:center;justify-content:center;background:var(--white)}

.footer-shape{top:1797px;left:0}
.footer{top:1924px;left:0;width:1200px;height:335px;background:var(--dark)}
.foot-brand{left:130px;top:1968px;display:flex;align-items:center;gap:7px;font-family:"Raleway",sans-serif;font-weight:800;font-size:15px;color:var(--white);text-transform:uppercase}
.foot-brand .mark{width:24px;height:24px;background:var(--white)}
.foot-about{left:130px;top:2028px;width:210px;font-size:10.5px;line-height:16px;color:#e6e6e6}
.foot-social{left:130px;top:2097px;width:22px;height:22px;border-radius:50%;background:var(--red)}
.foot-col h5{font-family:"Oswald",sans-serif;font-weight:500;font-size:16px;color:var(--red);letter-spacing:.3px;margin-bottom:9px}
.foot-col li{list-style:none;font-size:10.5px;color:#eee;line-height:22.8px}
.contact-item{display:flex;gap:8px;font-size:10.5px;color:#eee;line-height:13px;margin-bottom:15px}
.contact-item .ring{flex:none;width:22px;height:22px;border-radius:50%;border:1px solid #bbb;display:flex;align-items:center;justify-content:center}
.divider{left:130px;top:2168px;width:940px;border-top:1px dashed #4a5458}
.copyright{top:2192px;font-size:10px;color:#eee}
.copyright em{font-style:normal;color:var(--red)}
</style>
</head>
<body>

<div class="abs topbar">
  <span class="social-dot"></span>
  <span class="mail">
    <svg width="11" height="8" viewBox="0 0 11 8"><rect x="0.5" y="0.5" width="10" height="7" fill="none" stroke="#fff"/><path d="M0.5 0.5 5.5 4.5 10.5 0.5" fill="none" stroke="#fff"/></svg>
    info@openpath-association.ch
  </span>
</div>

<header class="abs header">
  <div class="brand"><span class="mark"></span>OpenPath Association</div>
  <span class="nav" style="left:538px">Home</span>
  <span class="nav" style="left:609px">Our Achievements</span>
  <span class="nav" style="left:741px">Media</span>
  <span class="nav" style="left:812px">Events</span>
  <span class="nav active" style="left:886px">Contacts
    <svg width="30" height="8" viewBox="0 0 30 8"><path d="M1 2 7 7 13 2 19 7 25 2 29 5" fill="none" stroke="#c01a24" stroke-width="1.4"/></svg>
  </span>
  <span class="donate">DONATE</span>
</header>

<section class="abs hero">
  <div class="abs" style="inset:0" role="img" aria-label="Terrain map of the mountain region around the association"></div>
  <div class="hero-shade"></div>
  <h1>CONTACT <span>US</span></h1>
  <div class="crumb">Home | <b>Contact</b></div>
</section>

<h2 class="abs center title" style="top:420px">Contact Info</h2>
<p class="abs center" style="top:473px;font-size:13px;color:var(--ink)">Sed ut perspiciatis unde omnis iste natus error sit voluptatem</p>

<div class="abs card" style="left:130px">
  <div class="icon"><svg width="14" height="19" viewBox="0 0 14 19"><path d="M7 0C3 0 0 3 0 7c0 5 7 12 7 12s7-7 7-12c0-4-3-7-7-7zm0 9.5A2.5 2.5 0 1 1 7 4.5a2.5 2.5 0 0 1 0 5z" fill="#fff"/></svg></div>
  <h3>Location</h3>
  <p>1870 Montvallon - Alpes - Switzerland</p>
</div>
<div class="abs card featured" style="left:450px">
  <div class="icon"><svg width="18" height="18" viewBox="0 0 24 24"><path d="M6.6 10.8a15.1 15.1 0 0 0 6.6 6.6l2.2-2.2a1 1 0 0 1 1-.25 11.4 11.4 0 0 0 3.6.57 1 1 0 0 1 1 1V20a1 1 0 0 1-1 1A17 17 0 0 1 3 4a1 1 0 0 1 1-1h3.5a1 1 0 0 1 1 1c0 1.25.2 2.45.57 3.6a1 1 0 0 1-.25 1z" fill="#c01a24"/></svg></div>
  <h3>Phone</h3>
  <p>+41 (555) 240 6100</p>
</div>
<div class="abs card" style="left:770px">
  <div class="icon"><svg width="17" height="12" viewBox="0 0 17 12"><rect width="17" height="12" rx="1" fill="#fff"/><path d="M0.8 1 8.5 6.5 16.2 1" fill="none" stroke="#c01a24" stroke-width="1.3"/></svg></div>
  <h3>Email</h3>
  <p>info@openpath-association.ch</p>
</div>

<section class="abs enquiry"></section>
<p class="abs center eyebrow" style="top:818px">Get In Touch</p>
<h2 class="abs center title" style="top:838px">Have Any Question</h2>
<div class="abs field" style="left:203px;top:924px;width:392px;height:58px">Name:</div>
<div class="abs field" style="left:605px;top:924px;width:391px;height:58px;padding-left:16px">Phone:</div>
<div class="abs field" style="left:203px;top:993px;width:793px;height:58px">Email:</div>
<div class="abs field" style="left:203px;top:1062px;width:793px;height:137px">Comments:</div>
<div class="abs submit">SUBMIT</div>

<p class="abs center eyebrow" style="top:1375px">Committee</p>
<h2 class="abs center title" style="top:1395px">Our Team Member</h2>

<div class="abs arrow" style="left:48px"><svg width="8" height="10" viewBox="0 0 8 10"><path d="M6 1 2 5 6 9" fill="none" stroke="#222" stroke-width="1.6"/></svg></div>
<div class="abs arrow" style="left:1117px"><svg width="8" height="10" viewBox="0 0 8 10"><path d="M2 1 6 5 2 9" fill="none" stroke="#222" stroke-width="1.6"/></svg></div>

<div class="abs member" style="left:130px">
  <div class="photo" role="img" aria-label="Portrait of Margarate Nobel" style="background:linear-gradient(160deg,#6d7a55,#9a6a4a 55%,#c9a27c)"></div>
  <h4>Margarate Nobel</h4><span>Team Management</span>
</div>
<div class="abs member" style="left:370px">
  <div class="photo" role="img" aria-label="Portrait of Danial Offence" style="background:linear-gradient(170deg,#d8d6d1,#c2bdb5 55%,#4a4f3a)"></div>
  <h4>Danial Offence</h4><span>Management</span>
</div>
<div class="abs member" style="left:610px">
  <div class="photo" role="img" aria-label="Portrait of Pitbul Simmulate" style="background:linear-gradient(170deg,#b9c2c9,#9aa3aa 50%,#1f2530)"></div>
  <h4>Pitbul Simmulate</h4><span>Team Management</span>
</div>
<div class="abs member" style="left:850px">
  <div class="photo" role="img" aria-label="Portrait of Alexa Gradian" style="background:linear-gradient(170deg,#b4aba4,#c9a27a 50%,#2a2523)"></div>
  <h4>Alexa Gradian</h4><span>Team Management</span>
</div>

<svg class="abs footer-shape" width="1200" height="128" viewBox="0 0 1200 128"><polygon points="0,55 472,127 1200,0 1200,128 0,128" fill="#263034"/></svg>
<footer class="abs footer"></footer>

<div class="abs foot-brand"><span class="mark"></span>OpenPath Association</div>
<p class="abs foot-about">Sed ut perspiciatis unde omnis iste natus error sit voluptatem accusantium rem aperiam</p>
<span class="abs foot-social"></span>

<div class="abs foot-col" style="left:450px;top:1962px">
  <h5>SITEMAP</h5>
  <ul><li>Home</li><li>Our Achivements</li><li>Media</li><li>Events</li><li>Contact Us</li></ul>
</div>
<div class="abs foot-col" style="left:670px;top:1962px">
  <h5>OTHERS</h5>
  <ul><li>Privacy Policy</li><li>Terms &amp; Conditions</li><li>Leagal</li><li>Donate</li><li>Help / Support</li></ul>
</div>
<div class="abs foot-col" style="left:876px;top:1962px;width:200px">
  <h5>CONTACTS</h5>
  <div class="contact-item" style="margin-top:3px">
    <span class="ring"><svg width="8" height="11" viewBox="0 0 14 19"><path d="M7 0C3 0 0 3 0 7c0 5 7 12 7 12s7-7 7-12c0-4-3-7-7-7z" fill="#c01a24"/></svg></span>
    <span>Chemin des Alpes 12 / 1870<br>Montvallon</span>
  </div>
  <div class="contact-item">
    <span class="ring"><svg width="10" height="7" viewBox="0 0 17 12"><rect width="17" height="12" rx="1" fill="#c01a24"/></svg></span>
    <span style="padding-top:4px">info@openpath-association.ch</span>
  </div>
</div>

<div class="abs divider"></div>
<p class="abs center copyright">Copyright © 2022 <em>OpenPath Association</em>. All Rights Reserved.</p>

</body>
</html>
```